Simple Logo Design for Semi-Clear Plastic Frosted Card stock

Create a business card on frosted plastic. compliment existing logo elements with a tree trunk, roots, or seed at the lower half and the full logo both on the front.

Contact information will go on a solid portion of the back of this design since this card stock is semi-transparent.

It is important to consider this plastic card stock medium in your design. I found helpful tips and guides listed at vellaprint-sample.net: be careful to understand ink printed on plastic cards cannot have too much of a consistent print area or risks peeling and fine lines can easily scratch off.
Updates

2" x 3.5" 20PT Clear Plastic Business cards with Round corners Please get info or templates here: https://www.vellaprint-sample.net/product-detail/2-x-35-20pt-clear-plastic-business-cards-with-round-corners

Target Market(s)

Not for profit- religion

Industry/Entity Type

Business

Must include complementary elements to the existing logo

Font styles to use
Decorative

Colors
000000

Requirements
Must have
• Elements of community, nature and oneness. Such as: seed, roots, tree trunk, etc.
• Three lines of space on the back for Name, Title, Phone Number.
Nice to have
• I like a light use of decorative elements
Should not have
• No eyes, from faces or animals.

```html
<!DOCTYPE html>
<html lang="en">
<head>
<meta charset="utf-8">
<title>Rootward Path – Frosted Plastic Business Card</title>
<link rel="stylesheet" href="https://fonts.googleapis.com/css2?family=Lato:wght@300;400;700;900&display=swap">
<style>
  :root {
    --page-bg: #e9e6e1;
    --frost-light: #f4f5f3;
    --frost-mid: #dfe3e0;
    --frost-edge: #cfd5d2;
    --panel-dark: #0d3a36;
    --panel-deep: #082b28;
    --vine-green: #2f7a2c;
    --vine-soft: #4c9a3a;
    --brand-green: #1f6b2a;
    --tag-ink: #1b1b1b;
    --name-ink: #e6ebe4;
    --detail-ink: #c9d3cc;
  }
  * { box-sizing: border-box; margin: 0; padding: 0; }
  html, body {
    width: 1200px;
    height: 969px;
    overflow: hidden;
    background: var(--page-bg);
  }
  .canvas {
    position: relative;
    width: 1200px;
    height: 969px;
  }
  .card {
    position: absolute;
    left: 100px;
    top: 199px;
    width: 1000px;
    height: 571px;
    border-radius: 38px;
    overflow: hidden;
    background: linear-gradient(135deg, var(--frost-light) 0%, var(--frost-mid) 60%, var(--frost-edge) 100%);
    box-shadow: 0 18px 40px rgba(0,0,0,0.18), inset 0 0 0 2px rgba(255,255,255,0.6);
  }
  .card-art {
    position: absolute;
    inset: 0;
    width: 100%;
    height: 100%;
  }
  .brand {
    position: absolute;
    left: 28px;
    top: 212px;
    width: 380px;
    text-align: center;
    font-family: "Lato", sans-serif;
  }
  .brand-mark {
    display: block;
    width: 96px;
    height: 96px;
    margin: 0 auto 18px;
    border-radius: 50%;
    background: var(--brand-green);
  }
  .brand-name {
    font-size: 38px;
    font-weight: 900;
    letter-spacing: 0.5px;
    color: var(--brand-green);
    line-height: 1;
    white-space: nowrap;
  }
  .brand-tagline {
    margin-top: 6px;
    font-size: 12px;
    font-weight: 700;
    letter-spacing: 1.2px;
    color: var(--tag-ink);
    text-transform: uppercase;
    white-space: nowrap;
  }
  .contact {
    position: absolute;
    right: 48px;
    top: 232px;
    text-align: right;
    font-family: "Lato", sans-serif;
    white-space: nowrap;
  }
  .contact-name {
    font-size: 38px;
    font-weight: 700;
    letter-spacing: 2px;
    color: var(--name-ink);
  }
  .contact-title {
    margin-top: 8px;
    font-size: 30px;
    font-weight: 300;
    color: var(--detail-ink);
  }
  .contact-phone {
    margin-top: 12px;
    font-size: 34px;
    font-weight: 300;
    letter-spacing: 1px;
    color: var(--name-ink);
  }
</style>
</head>
<body>
<main class="canvas">
  <section class="card">
    <svg class="card-art" viewBox="0 0 1000 571" preserveAspectRatio="none" aria-hidden="true">
      <defs>
        <linearGradient id="panelFill" x1="0" y1="0" x2="1" y2="1">
          <stop offset="0" stop-color="var(--panel-dark)"/>
          <stop offset="1" stop-color="var(--panel-deep)"/>
        </linearGradient>
        <linearGradient id="vineFill" x1="0" y1="0" x2="0" y2="1">
          <stop offset="0" stop-color="var(--vine-soft)" stop-opacity="0.35"/>
          <stop offset="1" stop-color="var(--vine-green)" stop-opacity="0.6"/>
        </linearGradient>
      </defs>
      <path class="solid-panel" d="M 430 0 C 390 160, 400 360, 500 571 L 1000 571 L 1000 0 Z" fill="url(#panelFill)"/>
    </svg>
    <svg class="card-art" viewBox="0 0 1000 571" preserveAspectRatio="none" role="img" aria-label="Climbing vine with leaves rising along the curved edge of the dark panel">
      <path class="vine-area" d="M 440 60 C 470 40, 640 0, 760 30 C 700 110, 640 250, 570 571 L 510 571 C 450 420, 430 240, 440 60 Z" fill="url(#vineFill)"/>
    </svg>
    <div class="brand">
      <span class="brand-mark"></span>
      <p class="brand-name">ROOTWARD PATH</p>
      <p class="brand-tagline">Growth, Fellowship &amp; Calm</p>
    </div>
    <div class="contact">
      <p class="contact-name">ELIAS MARREN</p>
      <p class="contact-title">CEO/Founder</p>
      <p class="contact-phone">555 014 2290</p>
    </div>
  </section>
</main>
</body>
</html>
```